Bramble firearms training and consulting

Business card for a new firearms training company. I train persons on firearms safety, personal protection, shooting tactics and CHL.Im a Prior State trooper. I also served 4 years in IRaq as a Protection contractor with the Dept of State. Real world training for Real world situations. I would like the company name to be, BRAMBLE FIREARMS TRAINING AND CONSULTING. Im native american also. Ive provided pics. Put the name Bramble above the arrowhead but rotate the arrowhead to the right with it pointing right. Then place bramble inside the arrowhead. lets see both.
Industry/Entity Type
Business
Contact Information for Business Card
Christian Chatellier817-240-0488shadowtraining33@gmail.com

```html
<!DOCTYPE html>
<html lang="en">
<head>
<meta charset="utf-8">
<title>Bramble Firearms Training and Consulting – Business Card</title>
<link rel="stylesheet" href="https://fonts.googleapis.com/css2?family=Fondamento&family=Arimo:wght@400;700&display=swap">
<style>
  :root {
    --stage: #161616;
    --card: #f3f3f1;
    --brand-red: #7e1a10;
    --tagline-red: #8b1f14;
    --ink: #111111;
  }
  * { margin: 0; padding: 0; box-sizing: border-box; }
  html, body {
    width: 1200px;
    height: 1141px;
    overflow: hidden;
    background: var(--stage);
  }
  .card {
    position: absolute;
    left: 250px;
    top: 4px;
    width: 686px;
    height: 1125px;
    background: var(--card);
  }
  .band {
    position: absolute;
    left: 179px;
    width: 330px;
    background: var(--brand-red);
  }
  .band-top { top: 0; height: 45px; }
  .band-top-rule { top: 50px; height: 4px; }
  .band-bottom-rule { top: 1067px; height: 4px; }
  .band-bottom { top: 1076px; height: 49px; }

  .holder {
    position: absolute;
    top: 112px;
    width: 100%;
    text-align: center;
    font-family: "Fondamento", serif;
    color: var(--ink);
  }
  .holder-name { font-size: 52px; line-height: 1; font-weight: 400; }
  .holder-role { font-size: 21px; line-height: 1; margin-top: 4px; }

  .brand {
    position: absolute;
    top: 468px;
    width: 100%;
    display: flex;
    justify-content: center;
    align-items: center;
    gap: 22px;
  }
  .brand-mark {
    width: 34px;
    height: 34px;
    background: var(--brand-red);
  }
  .brand-name {
    font-family: "Arimo", sans-serif;
    font-weight: 700;
    font-size: 76px;
    letter-spacing: 4px;
    color: var(--brand-red);
    line-height: 1;
  }
  .tagline {
    position: absolute;
    top: 622px;
    width: 100%;
    text-align: center;
    font-family: "Arimo", sans-serif;
    font-size: 27px;
    color: var(--tagline-red);
    letter-spacing: 0.3px;
  }

  .contact {
    position: absolute;
    top: 903px;
    left: 0;
    width: 100%;
    list-style: none;
    font-family: "Fondamento", serif;
    font-size: 31px;
    color: var(--ink);
  }
  .contact-line {
    display: flex;
    justify-content: center;
    align-items: center;
    gap: 14px;
    height: 43px;
  }
  .contact-icon { width: 30px; height: 30px; flex: none; }
</style>
</head>
<body>
  <main class="card">
    <div class="band band-top"></div>
    <div class="band band-top-rule"></div>

    <header class="holder">
      <h1 class="holder-name">Dorian Pellwick</h1>
      <p class="holder-role">Trainer and Consultant</p>
    </header>

    <div class="brand">
      <span class="brand-mark"></span>
      <span class="brand-name">BRAMBLE</span>
    </div>
    <p class="tagline">FIREARMS TRAINING AND CONSULTING</p>

    <ul class="contact">
      <li class="contact-line">
        <svg class="contact-icon" viewBox="0 0 30 30" aria-hidden="true">
          <circle cx="15" cy="15" r="13" fill="none" stroke="#111" stroke-width="2.2"/>
          <path d="M10 8.5c1-.8 2-.6 2.6.4l1.3 2.2c.4.8.2 1.6-.6 2.1l-.8.5c.8 1.8 2 3 3.8 3.8l.5-.8c.5-.8 1.3-1 2.1-.6l2.2 1.3c1 .6 1.2 1.6.4 2.6-1.3 1.5-3 1.8-5 .8-3.4-1.7-5.9-4.2-7.600-7.6-1-2-.7-3.7.8-5z" fill="#111"/>
        </svg>
        <span>555-317-9062</span>
      </li>
      <li class="contact-line">
        <svg class="contact-icon" viewBox="0 0 30 30" aria-hidden="true">
          <circle cx="15" cy="15" r="13" fill="none" stroke="#111" stroke-width="2.2"/>
          <rect x="8" y="10" width="14" height="10" rx="1.5" fill="#111"/>
          <path d="M8.5 10.8l6.5 5 6.5-5" fill="none" stroke="#f3f3f1" stroke-width="1.4"/>
        </svg>
        <span>bramblecourse58@mailvento.com</span>
      </li>
      <li class="contact-line">
        <svg class="contact-icon" viewBox="0 0 30 30" aria-hidden="true">
          <circle cx="15" cy="15" r="13" fill="none" stroke="#111" stroke-width="2.2"/>
          <path d="M15 7.5l-8 7h2.5v7h4v-4.5h3v4.5h4v-7H23z" fill="#111"/>
        </svg>
        <span>48 Alder Lane Fenwick, OR 97512</span>
      </li>
    </ul>

    <div class="band band-bottom-rule"></div>
    <div class="band band-bottom"></div>
  </main>
</body>
</html>
```